Business card design for a teacher - double sided, sleek design.

My name is Lina and I am an online Arabic language teacher. I am looking for a beautiful business card design for my online teaching business.

The cards will be printed in 85mm x 55mm size.
The card can be either portrait or landscape.

The design should contain my logo on one side and information on the other.

The design needs to be clean and modern. Use of subtle Arabic geometric patterns would be nice. Icons for the social media information on the card should also match the design theme.

My logo font is Consolas, which is a Monospace font.

Business card design should be delivered with editable PSD or EPS files in the handover.

Thanks

Lina

----

Information on the back:

URL: www.speakwithnadia.net [this should stand out more than other details]
Email: info@speakwithnadia.net
Instagram: @speakwithnadia
Facebook: facebook.com/speakwithnadia
Skype: speakwithnadia

My brand colours are shown in the logo attached. These are:
- Teal green - 4DC9C1
- Mango yellow - FFD600

Target Market(s)

- Young professionals
- Expatriates
- Women and Men

Industry/Entity Type

Education

Contact Information for Business Card

Information on the back:

Skype: speakwithnadia

- Teal green - 4DC9C1
- Mango yellow - FFD600

Font styles to use
Other font styles liked:
• Any font complimentary to my logo font which is a Monospace font called Consolas.

Colors

Designer to choose colors to be used in the design.

Requirements
Must have
• - Aesthetically pleasing look
• - Complimentary design with existing logo
Nice to have
• Arabic geometrical patterns

```html
<!DOCTYPE html>
<html lang="en">
<head>
<meta charset="utf-8">
<title>Speak with Nadia – Business Cards</title>
<link rel="stylesheet" href="https://fonts.googleapis.com/css2?family=Arimo:wght@400;700&family=Inconsolata:wght@500&display=swap">
<style>
  :root {
    --bg: #2b2b2b;
    --card: #ffffff;
    --pattern-a: #ffffff;
    --pattern-b: #eceeee;
    --teal: #4dc9c1;
    --teal-dark: #3fb3ab;
    --mango: #ffd600;
    --ink: #555a5c;
    --ink-soft: #7b8082;
    --white: #ffffff;
  }
  * { box-sizing: border-box; margin: 0; padding: 0; }
  html, body { width: 1200px; height: 997px; overflow: hidden; }
  body {
    background: var(--bg);
    font-family: "Arimo", Arial, sans-serif;
    position: relative;
  }
  .card {
    position: absolute;
    top: 323px;
    width: 540px;
    height: 350px;
    background: var(--card);
    overflow: hidden;
    box-shadow: 0 18px 40px rgba(0,0,0,.45);
  }
  .card--front { left: 40px; }
  .card--back { left: 620px; }

  .card__pattern {
    position: absolute;
    inset: 0;
    background: radial-gradient(circle at 50% 40%, var(--pattern-a) 0%, var(--pattern-b) 100%);
  }

  .band {
    position: absolute;
    left: 0; right: 0;
    background: var(--teal);
    border-top: 3px solid var(--mango);
    border-bottom: 3px solid var(--mango);
  }

  /* Front: logo side */
  .front-logo {
    position: absolute;
    left: 46px; top: 96px;
    display: flex;
    align-items: center;
    gap: 22px;
  }
  .logo-square {
    width: 92px; height: 92px;
    border: 3px solid var(--mango);
    background: var(--teal);
    flex: none;
  }
  .brand-name {
    font-family: "Arimo", Arial, sans-serif;
    font-weight: 400;
    color: var(--ink);
    font-size: 40px;
    letter-spacing: 6px;
    line-height: 1.1;
    text-transform: uppercase;
  }
  .front .band { bottom: 34px; height: 54px; }
  .socials {
    position: absolute;
    left: 0; right: 0; bottom: 34px;
    height: 54px;
    display: flex;
    justify-content: space-around;
    align-items: center;
    list-style: none;
  }
  .socials li {
    display: flex; align-items: center; gap: 8px;
    color: var(--white);
    font-size: 15px;
    font-weight: 700;
  }
  .social-dot {
    width: 16px; height: 16px;
    border-radius: 50%;
    background: var(--teal-dark);
    border: 2px solid var(--white);
  }

  /* Back: info side */
  .back-logo {
    position: absolute;
    left: 50%; top: 26px;
    transform: translateX(-50%);
    display: flex; align-items: center; gap: 10px;
  }
  .back-logo .logo-square { width: 64px; height: 64px; }
  .back-logo .brand-name { font-size: 15px; letter-spacing: 3px; }
  .person {
    position: absolute;
    left: 0; right: 0; top: 114px;
    text-align: center;
  }
  .person__name {
    color: var(--teal);
    font-weight: 700;
    font-size: 22px;
    letter-spacing: 1px;
    display: inline-block;
    padding: 0 50px 3px;
    border-bottom: 2px solid var(--teal);
  }
  .person__role {
    color: var(--ink);
    font-size: 15px;
    margin-top: 4px;
  }
  .contact-icons {
    position: absolute;
    left: 50%; top: 196px;
    transform: translateX(-50%);
    display: flex; gap: 10px;
  }
  .contact-icons svg { width: 24px; height: 24px; }
  .contact-email {
    position: absolute;
    left: 0; right: 0; top: 232px;
    text-align: center;
    color: var(--ink);
    font-size: 17px;
  }
  .back .band { bottom: 36px; height: 50px; }
  .contact-web {
    position: absolute;
    left: 0; right: 0; bottom: 36px;
    height: 50px;
    display: flex; align-items: center; justify-content: center;
    color: var(--white);
    font-weight: 700;
    font-size: 18px;
    letter-spacing: 1px;
  }
</style>
</head>
<body>

<section class="card card--front front" aria-label="Card front">
  <div class="card__pattern" role="img" aria-label="Subtle Arabic geometric star pattern"></div>
  <div class="front-logo">
    <div class="logo-square"></div>
    <div class="brand-name">Speak<br>with Nadia</div>
  </div>
  <div class="band"></div>
  <ul class="socials">
    <li><span class="social-dot"></span>@speakwithnadia</li>
    <li><span class="social-dot"></span>speakwithnadia</li>
    <li><span class="social-dot"></span>speakwithnadia</li>
  </ul>
</section>

<section class="card card--back back" aria-label="Card back">
  <div class="card__pattern" role="img" aria-label="Subtle Arabic geometric star pattern"></div>
  <div class="back-logo">
    <div class="logo-square"></div>
    <div class="brand-name">Speak<br>with Nadia</div>
  </div>
  <div class="person">
    <div class="person__name">LINA</div>
    <div class="person__role">Online Arabic language teacher</div>
  </div>
  <div class="contact-icons">
    <svg viewBox="0 0 24 24" aria-label="Email">
      <circle cx="12" cy="12" r="12" fill="#4dc9c1"/>
      <rect x="6" y="8" width="12" height="8" fill="#fff"/>
      <path d="M6 8 L12 13 L18 8" fill="none" stroke="#4dc9c1" stroke-width="1.4"/>
    </svg>
    <svg viewBox="0 0 24 24" aria-label="Website">
      <circle cx="12" cy="12" r="12" fill="#4dc9c1"/>
      <g fill="none" stroke="#fff" stroke-width="1.3">
        <circle cx="12" cy="12" r="6"/>
        <ellipse cx="12" cy="12" rx="2.6" ry="6"/>
        <line x1="6" y1="12" x2="18" y2="12"/>
      </g>
    </svg>
  </div>
  <div class="contact-email">info@speakwithnadia.net</div>
  <div class="band"></div>
  <div class="contact-web">www.speakwithnadia.net</div>
</section>

</body>
</html>
```